Lorvex Tilo medical cannibis cultivation company

tag - Tilo rise
Lorvex Tilo medical cannabis cultivation - logo is selected- can we please see bold examples with our selection. We are mainly dealing with medical companies and professionals. We would like to be stand out in the crowd with our designs. Welcome any and all attempts. Thanks

Target Market(s)

Medical and Professional

Industry/Entity Type

Medical And Science

Font styles to use
Sans Serif

Colors

Designer to choose colors to be used in the design.

Requirements
Must have
• Bright colour and be bold- Love the teal and magenta that is currently on the dark background design.
Nice to have
• shading and the 3D affect- The shadowed appearance.
Should not have
• Anything related to illegal activity or un professional manners

```html
<!DOCTYPE html>
<html lang="en">
<head>
<meta charset="utf-8">
<title>Lorvex Tilo — Business Card</title>
<link href="https://fonts.googleapis.com/css2?family=Marcellus&family=Mulish:wght@700&family=Tinos&display=swap" rel="stylesheet">
<style>
  :root {
    --backdrop: #dcdcdc;
    --card: #ffffff;
    --teal: #00aee8;
    --magenta: #9b4a9a;
    --ring: #8b9196;
    --tagline: #8b9196;
    --ink-light: #ffffff;
  }
  html, body {
    margin: 0;
    width: 1125px;
    height: 1200px;
    overflow: hidden;
    background: var(--backdrop);
  }
  .canvas { position: relative; width: 1125px; height: 1200px; }
  .card {
    position: absolute;
    left: 166px;
    width: 800px;
    height: 457px;
    background: var(--card);
    border-radius: 26px;
    overflow: hidden;
  }
  .card--front { top: 103px; }
  .card--back { top: 619px; }

  .band {
    position: absolute;
    top: 77px;
    left: 0;
    width: 800px;
    height: 300px;
    background: var(--teal);
  }
  .band__accent {
    position: absolute;
    top: 0;
    right: 0;
    width: 186px;
    height: 300px;
    background: var(--magenta);
  }
  .contact {
    position: absolute;
    left: 62px;
    top: 124px;
    color: var(--ink-light);
  }
  .contact__name {
    font-family: "Mulish", sans-serif;
    font-weight: 700;
    font-size: 28px;
    letter-spacing: 0.5px;
    margin: 0;
    line-height: 1;
  }
  .contact__role {
    font-family: "Mulish", sans-serif;
    font-weight: 700;
    font-size: 17px;
    margin: 5px 0 0;
  }
  .contact__address {
    font-family: "Tinos", serif;
    font-size: 19px;
    line-height: 24px;
    margin: 18px 0 0;
  }
  .contact__list {
    list-style: none;
    margin: 12px 0 0;
    padding: 0;
    font-family: "Tinos", serif;
    font-size: 19px;
    line-height: 26px;
  }
  .contact__list li { display: flex; align-items: center; gap: 12px; }
  .contact__list svg { width: 17px; height: 17px; fill: var(--ink-light); }

  .seal { position: absolute; left: 404px; top: 75px; width: 330px; height: 310px; }
  .seal__name {
    position: absolute;
    left: 0; top: 0;
    width: 330px;
    height: 310px;
    display: flex;
    align-items: center;
    justify-content: center;
    font-family: "Marcellus", serif;
    font-size: 36px;
    color: var(--magenta);
  }

  .brand {
    position: absolute;
    left: 0;
    top: 128px;
    width: 800px;
    text-align: center;
  }
  .brand__mark { width: 170px; height: 150px; display: block; margin: 0 auto; }
  .brand__name {
    font-family: "Marcellus", serif;
    font-size: 50px;
    line-height: 1;
    color: var(--teal);
    margin: 0;
  }
  .brand__tagline {
    display: flex;
    align-items: center;
    justify-content: center;
    gap: 8px;
    margin-top: 4px;
    font-family: "Marcellus", serif;
    font-size: 20px;
    letter-spacing: 2px;
    color: var(--tagline);
    text-transform: uppercase;
  }
  .brand__tagline::before, .brand__tagline::after {
    content: "";
    width: 54px;
    height: 2px;
    background: var(--tagline);
  }
</style>
</head>
<body>
<div class="canvas">
  <section class="card card--front">
    <div class="band"><div class="band__accent"></div></div>
    <div class="contact">
      <h1 class="contact__name">MAREN HOLT</h1>
      <p class="contact__role">CEO/FOUNDER</p>
      <p class="contact__address">4120 Alder Court<br>Juneau, Alaska 34120</p>
      <ul class="contact__list">
        <li><svg viewBox="0 0 24 24"><path d="M6.6 10.8a15.1 15.1 0 0 0 6.6 6.6l2.2-2.2c.3-.3.7-.4 1-.2 1.1.4 2.3.6 3.6.6.6 0 1 .4 1 1V20c0 .6-.4 1-1 1A17 17 0 0 1 3 4c0-.6.4-1 1-1h3.5c.6 0 1 .4 1 1 0 1.3.2 2.5.6 3.6.1.3 0 .7-.2 1z"/></svg>555 201 4470</li>
        <li><svg viewBox="0 0 24 24"><path d="M2 5h20v14H2z M3.5 6.5 12 13l8.5-6.5" fill="none" stroke="#fff" stroke-width="2"/></svg>maren@lorvextilo.com</li>
        <li><svg viewBox="0 0 24 24"><circle cx="12" cy="12" r="10"/></svg>www.lorvextilo.com</li>
      </ul>
    </div>
    <div class="seal">
      <svg width="330" height="310" viewBox="0 0 330 310">
        <circle cx="165" cy="155" r="158" fill="#fff"/>
        <path d="M40 250 A150 150 0 1 1 290 250" fill="none" stroke="var(--ring)" stroke-width="8"/>
      </svg>
      <div class="seal__name">Lorvex Tilo</div>
    </div>
  </section>

  <section class="card card--back">
    <div class="brand">
      <svg class="brand__mark" viewBox="0 0 170 150">
        <circle cx="85" cy="78" r="68" fill="none" stroke="var(--ring)" stroke-width="5"/>
      </svg>
      <p class="brand__name">LORVEX TILO</p>
      <div class="brand__tagline">Tilo rise</div>
    </div>
  </section>
</div>
</body>
</html>
```